Social Media App Needs PPT Template

We need a PowerPoint template for a new social media company based in the DC area called "Bold Ledger." We provide an interactive digital platform for executives to share actionable advice. We would like to see designs that use our orange logo color as an accent, but are mainly grey, white, and black. The final design should communicate clean, chic, modern, and professional.

Target Market(s)

Executives

Industry/Entity Type

Information Technology

Font styles to use
Sans Serif

Colors
f78f20
fbe7d2
ffffff
000000
e8e8e8
757575

Requirements
Must have
• My project must have title page and many options for the body of the ppt (graphs, tables, etc). It also needs to be easy to modify. I must have someone who is experienced in creating powerpoint templates.
Nice to have
• It would be nice to have a very modern and clean design that includes the logo on every page, but still leaves a lot of room for the content of the slide
Should not have
• My design project should not look to busy.

```html
<!DOCTYPE html>
<html lang="en">
<head>
<meta charset="utf-8">
<title>Bold Ledger – About Our Company</title>
<link href="https://fonts.googleapis.com/css2?family=Lato:wght@300;400;700&display=swap" rel="stylesheet">
<style>
  :root {
    --orange: #f78f20;
    --navy: #222b3a;
    --stage: #cbcbcb;
    --white: #ffffff;
    --ink: #262c38;
    --muted: #757575;
    --rule-dark: #4a5366;
  }
  * { margin: 0; padding: 0; box-sizing: border-box; }
  html, body {
    width: 1200px; height: 960px; overflow: hidden;
    background: var(--stage);
    font-family: "Lato", sans-serif;
  }
  .page-label {
    position: absolute; top: 64px; left: 0; width: 1200px;
    text-align: center; color: var(--white);
    font-weight: 300; font-size: 32px; letter-spacing: 0.5px;
  }
  .slide {
    position: absolute; left: 120px; top: 143px;
    width: 958px; height: 719px; background: var(--white);
  }
  .sidebar {
    position: absolute; left: 0; top: 0; width: 170px; height: 100%;
    background: var(--navy);
  }
  .brand {
    position: absolute; top: 58px; left: 0; width: 170px;
    display: flex; flex-direction: column; align-items: center; gap: 14px;
  }
  .brand-dot {
    width: 40px; height: 40px; border-radius: 50%; background: var(--orange);
  }
  .brand-name {
    color: var(--white); font-weight: 700; font-size: 24px;
    letter-spacing: 1px; text-align: center; line-height: 1.1;
  }
  .site-url {
    position: absolute; left: 19px; bottom: 22px;
    color: var(--white); font-weight: 300; font-size: 17px;
  }
  .slide-title {
    position: absolute; left: 204px; top: 97px;
    color: var(--orange); font-weight: 400; font-size: 42px; line-height: 1;
  }
  .title-rule {
    position: absolute; left: 205px; top: 155px; width: 716px;
    height: 0; border-top: 1px solid var(--orange);
  }
  .column {
    position: absolute; top: 187px; width: 342px;
    font-size: 15.8px; line-height: 19.2px; color: var(--ink);
    text-align: justify; hyphens: auto; -webkit-hyphens: auto;
  }
  .column-left { left: 210px; }
  .column-right { left: 584px; }
  .column p + p { margin-top: 19.2px; }
  .lead { font-weight: 700; }
  .feature-image {
    position: absolute; left: 587px; top: 373px; width: 339px; height: 210px;
    background: radial-gradient(ellipse at 40% 55%, #5a6387 0%, #262a3a 35%, #0d0f14 75%);
  }
  .footer-rule {
    position: absolute; left: 802px; top: 664px; width: 124px;
    height: 1px; background: var(--rule-dark);
  }
  .page-number {
    position: absolute; right: 35px; top: 682px;
    color: var(--muted); font-size: 13px;
  }
</style>
</head>
<body>
  <div class="page-label">Page 2</div>

  <main class="slide">
    <aside class="sidebar">
      <div class="brand">
        <span class="brand-dot"></span>
        <span class="brand-name">Bold Ledger</span>
      </div>
      <div class="site-url">boldledger.com</div>
    </aside>

    <h1 class="slide-title">About Our Company</h1>
    <div class="title-rule"></div>

    <section class="column column-left">
      <p class="lead">Lorem ipsum dolor sit amet, consectetuer adipiscing elit, sed diam nonummy nibh euismod tincidunt ut laoreet dolore magna aliquam erat volutpat. Ut wisi enim ad minim veniam, quis nostrud exerci tation ullamcorper suscipit lobortis nisl ut aliquip ex ea commodo consequat.</p>
      <p>Duis autem vel eum iriure dolor in hendrerit in vulputate velit esse molestie consequat, vel illum dolore eu feugiat nulla facilisis at vero eros et accumsan et iusto odio dignissim qui blandit praesent luptatum zzril delenit augue duis dolore te feugait nulla facilisi. Nam liber tempor cum soluta nobis eleifend option congue nihil imperdiet doming id quod mazim placerat facer possim assum. Typi non habent claritatem insitam; est usus legentis in iis qui facit eorum claritatem. Investigationes demonstraverunt lectores legere me lius quod ii legunt saepius. Claritas est etiam processus dynamicus, qui sequitur mutationem consuetudium lectorum.</p>
    </section>

    <section class="column column-right">
      <p>Duis autem vel eum iriure dolor in hendrerit in vulputate velit esse molestie consequat, vel illum dolore eu feugiat nulla facilisis at vero eros et accumsan et iusto odio dignissim qui blandit praesent luptatum zzril delenit augue duis dolore te feugait nulla facilisi. Nam liber tempor cum soluta nobis eleifend option congue nihil imperdiet doming id quod mazim placerat facer possim assum.</p>
    </section>

    <div class="feature-image" role="img" aria-label="Businessman in a dark suit holding a smartphone with glowing social media icons rising from the screen"></div>

    <div class="footer-rule"></div>
    <div class="page-number">Page 1</div>
  </main>
</body>
</html>
```